Harborne Bus Card

i own a building in the bronx ny - its called "Harborne Residences"i want a classy logo / business card - nothing too religuous but it is like a family there - its a large apartment building - colors i like dark red, black, medium shade of gray also reg business card stuff tel # 914-555-0173 address 4738 Larkwell Ave Bronx NY 10499 Email fijosh@aol.comslogan - " Together we are home "i can send u a picture of the building for the backside

```html
<!DOCTYPE html>
<html lang="en">
<head>
<meta charset="utf-8">
<title>Harborne Residences — Business Card</title>
<link href="https://fonts.googleapis.com/css2?family=Open+Sans:wght@400;600;700&display=swap" rel="stylesheet">
<style>
  :root {
    --backdrop: #3a3330;
    --card-black: #0d0d0d;
    --brand-red: #d3161b;
    --text-light: #d6d6d6;
    --silver: #a9a9a9;
    --divider: #2e2e2e;
  }
  * { margin: 0; padding: 0; box-sizing: border-box; }
  html, body {
    width: 1200px;
    height: 844px;
    overflow: hidden;
    background: var(--backdrop);
    font-family: "Open Sans", Arial, sans-serif;
  }
  .stage {
    position: relative;
    width: 1200px;
    height: 844px;
    display: flex;
    align-items: center;
    justify-content: center;
    gap: 60px;
  }
  .card {
    position: relative;
    width: 525px;
    height: 300px;
    background: var(--card-black);
    border-radius: 3px;
    box-shadow: 0 12px 30px rgba(0,0,0,0.45);
  }
  .brand-name {
    display: flex;
    align-items: center;
    font-weight: 700;
    line-height: 1.1;
    white-space: nowrap;
  }
  .brand-mark { flex: none; }

  /* Front side */
  .card-front .brand-name {
    position: absolute;
    left: 40px;
    top: 98px;
    gap: 10px;
    color: var(--brand-red);
    font-size: 22px;
  }
  .card-front .brand-mark {
    width: 14px;
    height: 14px;
    background: var(--brand-red);
  }
  .card-front .divider {
    position: absolute;
    left: 252px;
    top: 48px;
    width: 1px;
    height: 150px;
    background: var(--divider);
  }
  .contact {
    position: absolute;
    left: 278px;
    top: 56px;
    color: var(--text-light);
    font-size: 13px;
    line-height: 1.4;
  }
  .contact .person-name {
    color: var(--brand-red);
    font-weight: 600;
    font-size: 15px;
    letter-spacing: 0.3px;
    text-transform: uppercase;
  }
  .contact .person-title { margin-bottom: 4px; }
  .contact .line { display: flex; align-items: center; gap: 6px; }
  .contact .line svg { flex: none; }
  .contact .address { margin-top: 10px; }
  .slogan {
    position: absolute;
    left: 0;
    right: 0;
    bottom: 34px;
    text-align: center;
    color: var(--brand-red);
    font-weight: 600;
    font-size: 13px;
    letter-spacing: 2px;
    text-transform: uppercase;
  }

  /* Back side */
  .card-back {
    display: flex;
    align-items: center;
    justify-content: center;
  }
  .card-back .brand-name {
    gap: 14px;
    color: var(--silver);
    font-size: 36px;
  }
  .card-back .brand-mark {
    width: 22px;
    height: 22px;
    background: var(--silver);
  }
</style>
</head>
<body>
<main class="stage">
  <section class="card card-front" aria-label="Business card front">
    <div class="brand-name"><span class="brand-mark"></span><span>Harborne<br>Residences</span></div>
    <div class="divider"></div>
    <div class="contact">
      <div class="person-name">Daniel Whitmore</div>
      <div class="person-title">Managing Director</div>
      <div class="line">
        <svg width="10" height="10" viewBox="0 0 10 10" aria-hidden="true"><path d="M1 3c0-1 1-2 2-2h4c1 0 2 1 2 2v1H7V3H3v1H1zM2 5h6l1 4H1z" fill="var(--brand-red)"/></svg>
        <span>914-555-0173</span>
      </div>
      <div class="line">
        <svg width="10" height="8" viewBox="0 0 10 8" aria-hidden="true"><rect width="10" height="8" fill="var(--brand-red)"/><path d="M0 0l5 4 5-4" stroke="var(--card-black)" fill="none"/></svg>
        <span>mavreld@quintmail.com</span>
      </div>
      <div class="address">4738 Larkwell Ave<br>Bronx NY 10499</div>
    </div>
    <div class="slogan">Together we are home</div>
  </section>

  <section class="card card-back" aria-label="Business card back">
    <div class="brand-name"><span class="brand-mark"></span><span>Harborne<br>Residences</span></div>
  </section>
</main>
</body>
</html>
```